We need a complete design for our construction company KELTO CONSTRUCTION based in Auckland New Zealand, we need a logo, website, business card, vehicle design etc..
We are a mid to high-end construction company who work mostly on residential projects and some commercial.

What we want to see in the design;
Professional,
Architectural,
Simple,
Alternative,

We want the design to communicate professionalism, high quality wormanship and and quality service.

Target Market(s)

People looking for a quality building/ construction company

Industry/Entity Type

Construction Company

Contact Information for Business Card

KELTO CONSTRUCTION.co.nz
Lino Verasek
lino@keltoconstruction.example.nz
021 5807 462

Logo Text

KELTO CONSTRUCTION

Number of Pages Required

5+ page

Font styles to use
Sans Serif

Colors

Designer to choose colors to be used in the design.

Requirements
Must have
• Must appear high end, professional, quality, be simple, easy to use, give security to potential clients
Nice to have
• high-quality photos of our recent projects
• about us page
• blog page
• contact us page
• high quality content
Should not have
• should not be hard to use and have too much going on.

```html
<!DOCTYPE html>
<html lang="en">
<head>
<meta charset="utf-8">
<title>Kelto Construction</title>
<link rel="stylesheet" href="https://fonts.googleapis.com/css2?family=Mulish:wght@400;600;700;800&family=Open+Sans:ital,wght@0,400;0,600;1,400&display=swap">
<style>
:root{
  --yellow:#f9cd1f;
  --yellow-soft:#fbd84a;
  --yellow-mid:#fad239;
  --yellow-deep:#f8c700;
  --dark:#333333;
  --darker:#2b2b2b;
  --text:#3a3a3a;
  --muted:#7a7a7a;
  --line:#dcdcdc;
  --white:#ffffff;
  --feature-text:#6a5a22;
}
*{margin:0;padding:0;box-sizing:border-box}
html,body{width:1200px;height:3120px;overflow:hidden;background:var(--white)}
body{font-family:"Open Sans",Arial,sans-serif;color:var(--text);position:relative}
h1,h2,h3,.brand,.nav a,.btn,.tabs span,.feature p{font-family:"Mulish",Arial,sans-serif}

/* header */
.site-header{position:absolute;top:0;left:0;width:1200px;height:125px;background:var(--white);border-top:5px solid var(--yellow)}
.brand{position:absolute;display:flex;align-items:center;gap:14px;font-weight:800;letter-spacing:2px;white-space:nowrap}
.brand .mark{width:22px;height:22px;display:block;flex:none}
.site-header .brand{left:79px;top:38px;font-size:30px;color:var(--yellow)}
.site-header .brand .mark{background:var(--yellow)}
.nav{position:absolute;right:0;top:-5px;height:130px;display:flex;align-items:center;left:636px}
.nav a{display:flex;align-items:center;justify-content:center;height:100%;font-size:15px;color:#777;text-decoration:none;letter-spacing:.5px}
.nav a.active{background:var(--yellow);color:var(--white);width:84px}
.nav a.n-about{margin-left:26px;width:60px}
.nav a.n-projects{margin-left:34px;width:82px}
.nav a.n-blog{margin-left:34px;width:46px}
.nav a.n-contact{margin-left:34px;width:80px}

/* hero */
.hero{position:absolute;top:125px;left:0;width:1200px;height:561px;background:linear-gradient(120deg,#6b675f 0%,#8c8575 35%,#a49b83 55%,#7c7a76 80%,#5d5f62 100%)}
.hero::after{content:"";position:absolute;inset:0;background:rgba(40,40,40,.35)}
.hero h1{position:absolute;left:0;width:1200px;top:200px;text-align:center;color:var(--white);font-size:66px;font-weight:700;line-height:86px;z-index:2}
.bracket{position:absolute;width:54px;height:241px;top:160px;border:4px solid rgba(220,220,220,.85);z-index:2}
.bracket.left{left:191px;border-right:none}
.bracket.right{left:963px;border-left:none}

/* about */
.about{position:absolute;top:686px;left:0;width:1200px;height:452px}
.about .photo{position:absolute;left:79px;top:32px;width:316px;height:420px;background:linear-gradient(180deg,#f5d44a 0%,#e8e2d6 22%,#3f4a7a 55%,#2a325e 100%);border-radius:40% 40% 0 0}
.corner{position:absolute;width:34px;height:34px;border-top:3px solid var(--yellow);border-left:3px solid var(--yellow)}
.about .corner{left:480px;top:76px}
.section-title{font-size:40px;font-weight:700;color:var(--text)}
.section-title em{font-style:normal;color:var(--yellow)}
.about h2{position:absolute;left:512px;top:112px}
.about p{position:absolute;left:512px;top:174px;width:604px;font-size:13.6px;line-height:25px;color:var(--muted)}
.btn{position:absolute;left:510px;top:327px;width:178px;height:46px;border:2px solid var(--yellow);display:flex;align-items:center;justify-content:center;font-size:19px;font-weight:600;color:var(--text)}

/* features */
.features{position:absolute;top:1138px;left:0;width:1200px;height:270px;display:flex}
.feature{width:400px;height:100%;display:flex;flex-direction:column;align-items:center;padding-top:42px}
.feature:nth-child(1){background:var(--yellow-soft)}
.feature:nth-child(2){background:var(--yellow-mid)}
.feature:nth-child(3){background:var(--yellow-deep)}
.feature svg{width:88px;height:88px}
.feature p{margin-top:24px;font-size:26px;font-weight:600;line-height:37px;color:var(--feature-text);text-align:center}

/* projects */
.projects{position:absolute;top:1408px;left:0;width:1200px;height:689px;background:var(--dark)}
.projects .corner{left:77px;top:42px}
.projects h2{position:absolute;left:104px;top:65px;color:var(--white)}
.tabs{position:absolute;left:104px;top:134px;display:flex;font-size:18px;color:#aaa}
.tabs span.on{color:var(--white);font-weight:700}
.tabs span:nth-child(2){margin-left:57px}
.tabs span:nth-child(3){margin-left:84px}
.tab-line{position:absolute;left:0;top:176px;width:1200px;height:20px}
.gallery{position:absolute;left:77px;top:225px;width:1046px;height:312px;display:flex}
.gallery div{flex:1;height:100%}
.g1{background:linear-gradient(180deg,#2f64b5 0%,#7aa6dc 35%,#b88a6f 55%,#8c6a52 85%,#5a5a55 100%)}
.g2{background:linear-gradient(180deg,#4a4640 0%,#c9875c 35%,#8f8fa0 60%,#b8b2a8 100%)}
.g3{background:linear-gradient(160deg,#eef0ef 0%,#d9dcdb 50%,#c9c5be 75%,#7b5a3e 100%)}
.arrow{position:absolute;top:570px;width:40px;height:40px;background:#4a4a4a;display:flex;align-items:center;justify-content:center}
.arrow.prev{left:79px}
.arrow.next{left:1083px}

/* blog */
.blog{position:absolute;top:2097px;left:0;width:1200px;height:649px;background:linear-gradient(180deg,#ffffff 0%,#f6f6f6 40%,#ececec 100%)}
.blog .corner{left:455px;top:44px}
.blog h2{position:absolute;left:0;width:1200px;top:66px;text-align:center}
.card{position:absolute;top:139px;width:324px;height:426px;border:1px solid var(--line);background:rgba(255,255,255,.55)}
.card .thumb{height:218px}
.card:nth-child(3){left:77px}
.card:nth-child(4){left:438px}
.card:nth-child(5){left:799px}
.t1{background:linear-gradient(180deg,#c98b62 0%,#b07454 40%,#6d7a4a 75%,#4f7a35 100%)}
.t2{background:linear-gradient(180deg,#5b93cf 0%,#b9cfe8 45%,#d4d44c 70%,#7a7a6a 100%)}
.t3{background:linear-gradient(180deg,#8fa8c4 0%,#3d6fb0 45%,#e9e9ea 80%,#c9cdd2 100%)}
.date{position:absolute;left:17px;top:150px;width:81px;height:83px;background:var(--yellow);display:flex;flex-direction:column;align-items:center;justify-content:center;color:var(--text);font-family:"Mulish",Arial,sans-serif}
.date b{font-size:32px;font-weight:600;line-height:34px}
.date small{font-size:14px;font-weight:600}
.card h3{margin:38px 16px 0;font-size:17px;font-weight:700;line-height:30px;color:var(--text)}
.card p{margin:12px 16px 0;font-size:13px;line-height:25px;color:var(--muted)}

/* footer */
.site-footer{position:absolute;top:2746px;left:0;width:1200px;height:312px;background:var(--yellow-soft)}
.site-footer .brand{left:79px;top:92px;font-size:21px;letter-spacing:1.5px;gap:12px;color:var(--white)}
.site-footer .brand .mark{background:var(--white);width:24px;height:24px}
.subscribe{position:absolute;left:77px;top:199px;width:324px;height:48px;border:1.5px solid #6a5a22;display:flex;align-items:center;justify-content:space-between;padding:0 16px}
.subscribe span{font-style:italic;font-size:13px;color:#6a5a22}
.site-footer h3{position:absolute;top:56px;font-size:22px;font-weight:600;color:#3f3a2a}
.sitemap h3{left:441px}
.sitemap ul{position:absolute;left:441px;top:108px;list-style:none}
.sitemap li{height:36px;font-size:13px;color:#4f4630;display:flex;align-items:flex-start}
.sitemap li::before{content:"";width:11px;height:11px;background:#4f4630;margin:3px 14px 0 0}
.contact h3{left:803px}
.contact .row{position:absolute;left:803px;display:flex;gap:14px;font-size:13.5px;line-height:25px;color:#4f4630}
.contact svg{flex:none;margin-top:4px}
.copyright{position:absolute;top:3058px;left:0;width:1200px;height:62px;background:var(--darker);color:#ddd;font-size:14px;display:flex;align-items:center;justify-content:center;letter-spacing:.3px}
</style>
</head>
<body>

<header class="site-header">
  <div class="brand"><span class="mark"></span>KELTO CONSTRUCTION</div>
  <nav class="nav">
    <a class="active" href="#">HOME</a>
    <a class="n-about" href="#">ABOUT</a>
    <a class="n-projects" href="#">PROJECTS</a>
    <a class="n-blog" href="#">BLOG</a>
    <a class="n-contact" href="#">CONTACT</a>
  </nav>
</header>

<section class="hero" role="img" aria-label="Builders in hard hats looking out over a city construction site">
  <span class="bracket left"></span>
  <span class="bracket right"></span>
  <h1>We Built your<br>Dreams</h1>
</section>

<section class="about">
  <div class="photo" role="img" aria-label="Smiling builder in a yellow hard hat and work gloves with arms crossed"></div>
  <span class="corner"></span>
  <h2 class="section-title">About <em>Us</em></h2>
  <p>Lorem Ipsum is simply dummy text of the printing and typesetting industry. Lorem Ipsum has been the industry's standard dummy text ever since the 1500s, when an unknown printer took a galley of type and scrambled it to make a type specimen book. It has survived not only five centuries, but also the leap into electronic typesetting, remaining essentially unchanged.</p>
  <a class="btn">CONTACT US</a>
</section>

<section class="features">
  <div class="feature">
    <svg viewBox="0 0 88 88" fill="none" stroke="#fff" stroke-width="4" stroke-linejoin="round">
      <path d="M10 16h40a8 8 0 0 1 8 8v14a8 8 0 0 1-8 8H28l-12 10v-10h-6a8 8 0 0 1-8-8V24a8 8 0 0 1 8-8z"/>
      <path d="M62 34h8a8 8 0 0 1 8 8v14a8 8 0 0 1-8 8h-4v9l-11-9H44a8 8 0 0 1-8-8v-6" fill="#fff"/>
      <circle cx="47" cy="57" r="3" fill="#fad239" stroke="none"/>
      <circle cx="57" cy="57" r="3" fill="#fad239" stroke="none"/>
      <circle cx="67" cy="57" r="3" fill="#fad239" stroke="none"/>
    </svg>
    <p>Communicate<br>professionalism</p>
  </div>
  <div class="feature">
    <svg viewBox="0 0 88 88" fill="none" stroke="#fff" stroke-width="4" stroke-linecap="round" stroke-linejoin="round">
      <circle cx="44" cy="44" r="38"/>
      <path d="M26 45l12 12 24-26"/>
    </svg>
    <p>High<br>quality wormanship</p>
  </div>
  <div class="feature">
    <svg viewBox="0 0 88 88" fill="none" stroke="#fff" stroke-width="3.5" stroke-linejoin="round">
      <circle cx="44" cy="36" r="28"/>
      <circle cx="44" cy="36" r="19"/>
      <path d="M44 24l3.5 7.5 8 1-6 5.5 1.5 8L44 42l-7 4 1.5-8-6-5.5 8-1z" fill="#fff"/>
      <path d="M28 58l-8 20 10-3 5 8 7-16M60 58l8 20-10-3-5 8-7-16"/>
    </svg>
    <p>And quality<br>service.</p>
  </div>
</section>

<section class="projects">
  <span class="corner"></span>
  <h2 class="section-title">Recent <em>Projects</em></h2>
  <div class="tabs"><span class="on">All</span><span>residential</span><span>commercial</span></div>
  <svg class="tab-line" viewBox="0 0 1200 20" fill="none" stroke="#f9cd1f" stroke-width="2">
    <path d="M0 1H100l17 17 17-17H1200"/>
  </svg>
  <div class="gallery">
    <div class="g1" role="img" aria-label="Brick and render residential apartment block"></div>
    <div class="g2" role="img" aria-label="Commercial building courtyard with glass facade at sunset"></div>
    <div class="g3" role="img" aria-label="Bright open-plan interior with timber floors"></div>
  </div>
  <div class="arrow prev"><svg width="14" height="20" viewBox="0 0 14 20"><path d="M10 3L4 10l6 7" fill="none" stroke="#f9cd1f" stroke-width="2.5"/></svg></div>
  <div class="arrow next"><svg width="14" height="20" viewBox="0 0 14 20"><path d="M4 3l6 7-6 7" fill="none" stroke="#f9cd1f" stroke-width="2.5"/></svg></div>
</section>

<section class="blog" aria-label="Latest blog posts">
  <span class="corner"></span>
  <h2 class="section-title">Latest <em>Blog</em></h2>
  <article class="card">
    <div class="thumb t1" role="img" aria-label="Two-storey family home lit at dusk"></div>
    <div class="date"><b>17</b><small>MAY</small></div>
    <h3>Lorem Ipsum is simply dummy text of the printing.</h3>
    <p>Lorem Ipsum is simply dummy text of the printing and typesetting industry. Lorem Ipsum has been the industry's standard.</p>
  </article>
  <article class="card">
    <div class="thumb t2" role="img" aria-label="Two engineers in hard hats reviewing plans on site"></div>
    <div class="date"><b>17</b><small>MAY</small></div>
    <h3>Lorem Ipsum is simply dummy text of the printing.</h3>
    <p>Lorem Ipsum is simply dummy text of the printing and typesetting industry. Lorem Ipsum has been the industry's standard.</p>
  </article>
  <article class="card">
    <div class="thumb t3" role="img" aria-label="Team gathered around blueprints on a table"></div>
    <div class="date"><b>17</b><small>MAY</small></div>
    <h3>Lorem Ipsum is simply dummy text of the printing.</h3>
    <p>Lorem Ipsum is simply dummy text of the printing and typesetting industry. Lorem Ipsum has been the industry's standard.</p>
  </article>
</section>

<footer class="site-footer">
  <div class="brand"><span class="mark"></span>KELTO CONSTRUCTION</div>
  <div class="subscribe">
    <span>Email Address</span>
    <svg width="26" height="22" viewBox="0 0 26 22"><path d="M1 10L25 1l-5 20-7-6-4 5v-7l12-10-15 9z" fill="#fff"/></svg>
  </div>
  <div class="sitemap">
    <h3>Sitemap</h3>
    <ul><li>Home</li><li>About</li><li>Project</li><li>Blog</li><li>Contact</li></ul>
  </div>
  <div class="contact">
    <h3>Contact Info</h3>
    <div class="row" style="top:100px">
      <svg width="16" height="20" viewBox="0 0 16 20"><path d="M8 1a7 7 0 0 0-7 7c0 5 7 11 7 11s7-6 7-11a7 7 0 0 0-7-7z" fill="#4f4630"/><circle cx="8" cy="8" r="2.6" fill="#fbd84a"/></svg>
      <span>Lorem ipsum dolor sit amet,<br>consectetur adipiscing elit.</span>
    </div>
    <div class="row" style="top:165px">
      <svg width="16" height="16" viewBox="0 0 16 16"><path d="M3 1l3 3-2 2c1 2 3 4 6 6l2-2 3 3-2 2C7 15 1 9 1 3z" fill="#4f4630"/></svg>
      <span>123 456 7890</span>
    </div>
    <div class="row" style="top:205px">
      <svg width="17" height="13" viewBox="0 0 17 13" fill="none" stroke="#4f4630" stroke-width="1.6"><rect x="1" y="1" width="15" height="11"/><path d="M1 1l7.5 6L16 1"/></svg>
      <span>info@keltoconstruction.example.nz</span>
    </div>
  </div>
</footer>

<div class="copyright">©KELTO CONSTRUCTIONS- 2018. All Rights Reserved.</div>

</body>
</html>
```